CREATE A BUSINESS CARD FOR A BOAT CLEANING SERVICE

WE ARE STARTING A NEW BOAT CLEANING BUSINESS. WE DIVE UNDERWATER TO CLEAN BOAT HULLS, JETTIES, UNDERWATER STRUCTURES ETC. WE ARE LOOKING FOR AN UPPERMARKET MODERN LOGO AND BUSINESS CARD AS ALOT OF OUR TARGET MARKET WILL BE HIGH END. YOU HAVE TO DESIGN A BUSINESS CARD AND LOGO SEPERATELY .
THE BUSINESS CARD DIMESNION MUST BE STANDARD SIZE.
The standard dimensions of a printed business card are 3.5 x 2 inches

Target Market(s)

UNDERWATER SERVICED

Industry/Entity Type

Business

Contact Information for Business Card

HOLLAND UNDERWATER SERVICES

Font styles to use
Serif

Colors

Designer to choose colors to be used in the design.

Requirements
Must have
• HOLLAND
Nice to have
• dark
Should not have
• more than 3 colors

```html
<!DOCTYPE html>
<html lang="en">
<head>
<meta charset="utf-8">
<title>Holland Underwater Service – Business Card</title>
<link href="https://fonts.googleapis.com/css2?family=Lato:wght@400;700&display=swap" rel="stylesheet">
<style>
  :root {
    --page: #ededed;
    --ink: #111111;
    --paper: #ffffff;
    --brand-blue: #1d5597;
    --grey-text: #6b6b6b;
    --light-text: #f2f2f2;
  }
  * { margin: 0; padding: 0; box-sizing: border-box; }
  html, body { width: 1200px; height: 900px; overflow: hidden; background: var(--page); }
  body { position: relative; font-family: 'Lato', sans-serif; }

  .card {
    position: absolute; top: 150px; width: 343px; height: 600px; overflow: hidden;
  }
  .card--front { left: 246px; background: var(--ink); }
  .card--back { left: 611px; background: var(--ink); }

  .front-divider { position: absolute; left: 0; top: 0; width: 343px; height: 300px; }

  .wordmark { position: absolute; left: 0; width: 100%; text-align: center; color: var(--brand-blue); font-weight: 400; }
  .wordmark__name { font-size: 30px; letter-spacing: 17px; padding-left: 17px; line-height: 1; }
  .wordmark__tag { font-size: 15.5px; letter-spacing: 4.2px; padding-left: 4px; margin-top: 12px; line-height: 1; }
  .card--front .wordmark { top: 110px; }
  .card--back .wordmark { top: 318px; }

  .contact { position: absolute; left: 33px; top: 320px; color: var(--light-text); }
  .contact__name { color: var(--brand-blue); font-size: 19.5px; letter-spacing: 0.5px; line-height: 1.2; }
  .contact__role { font-size: 17px; line-height: 1.2; }
  .contact__list { list-style: none; margin-top: 17px; font-size: 14.5px; line-height: 19.5px; }
  .contact__list li { display: flex; align-items: center; }
  .contact__list svg { width: 11px; height: 11px; margin-right: 14px; fill: var(--brand-blue); }
  .contact__address { margin-top: 17px; font-size: 14.5px; line-height: 19.5px; }
  .accent { color: var(--brand-blue); }

  .partners { position: absolute; left: 33px; top: 522px; display: flex; align-items: center; gap: 40px; }
  .partners__name { color: var(--light-text); font-size: 22px; font-weight: 700; line-height: 1; }
  .partners__badge { width: 66px; height: 44px; border-radius: 50%; background: #27526f; }

  .back-url { position: absolute; left: 0; width: 100%; top: 530px; text-align: center; color: var(--light-text); font-size: 15px; letter-spacing: 0.3px; }
</style>
</head>
<body>
  <section class="card card--front" aria-label="Business card front">
    <svg class="front-divider" viewBox="0 0 343 300" aria-hidden="true">
      <polygon points="0,0 343,0 343,178 0,262" fill="var(--paper)"/>
      <polygon points="0,262 343,178 343,196 0,278" fill="var(--brand-blue)"/>
      <polygon points="0,278 343,196 343,202 0,284" fill="var(--paper)"/>
    </svg>
    <div class="wordmark">
      <div class="wordmark__name">HOLLAND</div>
      <div class="wordmark__tag">UNDERWATER SERVICE</div>
    </div>

    <div class="contact">
      <div class="contact__name">SAM VERHOEF</div>
      <div class="contact__role">CEO / Founder</div>
      <ul class="contact__list">
        <li><svg viewBox="0 0 24 24"><path d="M6.6 10.8a15 15 0 0 0 6.6 6.6l2.2-2.2a1 1 0 0 1 1-.25 11.4 11.4 0 0 0 3.6.57 1 1 0 0 1 1 1V20a1 1 0 0 1-1 1A17 17 0 0 1 3 4a1 1 0 0 1 1-1h3.5a1 1 0 0 1 1 1c0 1.25.2 2.45.57 3.57a1 1 0 0 1-.25 1z"/></svg>212-555-0147</li>
        <li><svg viewBox="0 0 24 24"><path d="M2 5h20v14H2z M2 5l10 8 10-8" /></svg>info@hollandunderwaterservice.com</li>
        <li><svg viewBox="0 0 24 24"><path d="M12 2a10 10 0 1 0 0 20 10 10 0 0 0 0-20zm0 2c.9 0 2.2 2.2 2.6 6H9.4C9.8 6.2 11.1 4 12 4zM4.1 10h3.3a17 17 0 0 0 0 4H4.1a8 8 0 0 1 0-4zm5.3 4a15 15 0 0 1 0-4h5.2a15 15 0 0 1 0 4zm7.2 0a17 17 0 0 0 0-4h3.3a8 8 0 0 1 0 4zM12 20c-.9 0-2.2-2.2-2.6-4h5.2c-.4 1.8-1.7 4-2.6 4z"/></svg>www.<span class="accent">hollandunderwaterservice</span>.com</li>
      </ul>
      <div class="contact__address">Kaaistraat 8 4811XK<br>Breda, The Netherlands</div>
    </div>

    <div class="partners">
      <span class="partners__name">HOLLAND</span>
      <span class="partners__badge" role="img" aria-label="Partner badge"></span>
    </div>
  </section>

  <section class="card card--back" aria-label="Business card back">
    <div class="wordmark">
      <div class="wordmark__name">HOLLAND</div>
      <div class="wordmark__tag">UNDERWATER SERVICE</div>
    </div>
    <div class="back-url">www.<span class="accent">hollandunderwaterservice</span>.com</div>
  </section>
</body>
</html>
```